Business Card Design (NEW FILES)

ATTENTION: New vector files are available. Please update your design to reflect/use the new (better resolution) logo images.

Seeking a unique and professional business card design for a commercial drone photography/videography business. The layout should feature
the logo (attached) and include the following information:
Owen Tarrick
614-502-7738
www.skylarkreelworks.example
NRD Certified Remote Pilot

Owen Tarrick

```html
<!DOCTYPE html>
<html lang="en">
<head>
<meta charset="utf-8">
<title>Skylark Reelworks – Business Card</title>
<link rel="stylesheet" href="https://fonts.googleapis.com/css2?family=Montserrat:wght@500&family=Open+Sans:wght@400;700&display=swap">
<style>
  :root {
    --stage: #222222;
    --navy: #161a4a;
    --navy-deep: #121640;
    --orange: #f08a45;
    --white: #ffffff;
  }
  * { box-sizing: border-box; margin: 0; padding: 0; }
  html, body { width: 1200px; height: 780px; overflow: hidden; }
  body {
    background: var(--stage);
    font-family: "Open Sans", Arial, sans-serif;
    display: flex;
    align-items: center;
    justify-content: center;
    gap: 40px;
  }
  .card {
    position: relative;
    width: 560px;
    height: 320px;
    border-radius: 18px;
    background: linear-gradient(160deg, var(--navy) 0%, var(--navy-deep) 100%);
    border: 3px solid var(--orange);
    color: var(--white);
    overflow: hidden;
  }
  .brand {
    display: flex;
    align-items: center;
    gap: 12px;
    font-family: "Montserrat", Arial, sans-serif;
    font-weight: 500;
    color: var(--white);
    letter-spacing: 0.02em;
    text-transform: uppercase;
    line-height: 1;
  }
  .brand-dot {
    flex: none;
    border-radius: 50%;
    background: var(--orange);
  }
  .card-front .brand {
    position: absolute;
    left: 50%;
    top: 50%;
    transform: translate(-50%, -50%);
    font-size: 34px;
    white-space: nowrap;
  }
  .card-front .brand-dot { width: 30px; height: 30px; }

  .card-back .brand {
    position: absolute;
    left: 26px;
    top: 30px;
    font-size: 20px;
  }
  .card-back .brand-dot { width: 18px; height: 18px; }

  .owner {
    position: absolute;
    right: 34px;
    top: 26px;
    text-align: right;
  }
  .owner-name {
    font-weight: 700;
    font-size: 26px;
    color: var(--orange);
    line-height: 1.1;
  }
  .owner-role {
    font-size: 13px;
    color: var(--white);
  }
  .owner-bar {
    position: absolute;
    right: 0;
    top: 22px;
    width: 16px;
    height: 52px;
    background: var(--orange);
  }
  .credentials {
    position: absolute;
    left: 40px;
    bottom: 108px;
    font-size: 14px;
    line-height: 1.4;
  }
  .contact-list {
    position: absolute;
    left: 40px;
    bottom: 22px;
    list-style: none;
    font-size: 14px;
    line-height: 1.75;
  }
  .contact-list li { display: flex; align-items: center; gap: 10px; }
  .contact-icon { width: 14px; height: 14px; flex: none; }
</style>
</head>
<body>

  <section class="card card-front" aria-label="Card front">
    <div class="brand"><span class="brand-dot"></span>Skylark Reelworks</div>
  </section>

  <section class="card card-back" aria-label="Card back">
    <div class="brand"><span class="brand-dot"></span>Skylark Reelworks</div>

    <div class="owner">
      <p class="owner-name">Owen Tarrick</p>
      <p class="owner-role">Owner</p>
    </div>
    <span class="owner-bar"></span>

    <div class="credentials">
      <p>NRD Certified Remote Pilot</p>
      <p>Fully Insured</p>
    </div>

    <ul class="contact-list">
      <li>
        <svg class="contact-icon" viewBox="0 0 24 24" aria-hidden="true"><path fill="#f08a45" d="M6.6 10.8a15.1 15.1 0 0 0 6.6 6.6l2.2-2.2c.3-.3.7-.4 1-.2 1.1.4 2.3.6 3.6.6.6 0 1 .4 1 1V20c0 .6-.4 1-1 1A17 17 0 0 1 3 4c0-.6.4-1 1-1h3.5c.6 0 1 .4 1 1 0 1.3.2 2.5.6 3.6.1.3 0 .7-.2 1z"/></svg>
        614-502-7738
      </li>
      <li>
        <svg class="contact-icon" viewBox="0 0 24 24" aria-hidden="true"><circle cx="12" cy="12" r="9.5" fill="none" stroke="#f08a45" stroke-width="2"/><path d="M2.5 12h19M12 2.5c3 3 3 16 0 19M12 2.5c-3 3-3 16 0 19" fill="none" stroke="#f08a45" stroke-width="1.6"/></svg>
        www.skylarkreelworks.example
      </li>
      <li>
        <svg class="contact-icon" viewBox="0 0 24 24" aria-hidden="true"><rect x="2" y="5" width="20" height="14" rx="1.5" fill="none" stroke="#f08a45" stroke-width="2"/><path d="M3 6l9 7 9-7" fill="none" stroke="#f08a45" stroke-width="2"/></svg>
        info@skylarkreelworks.example
      </li>
    </ul>
  </section>

</body>
</html>
```